BildeVOLD buisnesscard

Hey :) I need a modern buisnesscard for my company BildeVOLD
It most have:
Dagligleder og Fotograf: Henrik Audun Strandvik

Mob: +4791264085
Epost: post@bildevold.example
Adresse: Kvernbakken9, 6040 Fjordvik

Facbook and instagram logo with text BildeVOLD

BildeVOLD logo

It Company

```html
<!DOCTYPE html>
<html lang="no">
<head>
<meta charset="utf-8">
<title>BildeVOLD – visittkort</title>
<link rel="stylesheet" href="https://fonts.googleapis.com/css2?family=Source+Sans+3:wght@400;600;700&display=swap">
<style>
  :root {
    --stage: #000000;
    --card: #4a4a4a;
    --text: #c6c6c6;
    --text-strong: #d2d2d2;
    --brand: #b4b4b4;
  }
  * { margin: 0; padding: 0; box-sizing: border-box; }
  html, body {
    width: 1200px; height: 900px; overflow: hidden;
    background: var(--stage);
    font-family: "Source Sans 3", sans-serif;
  }
  .stage { position: relative; width: 1200px; height: 900px; }
  .card {
    position: absolute; top: 275px; width: 477px; height: 293px;
    background: var(--card); color: var(--text);
  }
  .card--front { left: 116px; border-radius: 0 46px 0 46px; }
  .card--back  { left: 622px; border-radius: 46px 0 46px 0; }

  .holder { position: absolute; left: 20px; top: 43px; }
  .holder__name { font-size: 17px; font-weight: 600; color: var(--text-strong); margin-bottom: 6px; }
  .holder__address { font-size: 14px; line-height: 21px; font-style: normal; }

  .contact { position: absolute; right: 28px; top: 42px; list-style: none; text-align: right; }
  .contact__item { display: flex; justify-content: flex-end; align-items: center; gap: 9px; font-size: 13.5px; height: 20px; }
  .contact__item svg { width: 10px; height: 10px; fill: var(--text); }
  .contact__item--social { margin-top: 7px; font-weight: 700; font-size: 13px; }
  .contact__square { width: 16px; height: 16px; background: var(--text); border-radius: 2px; }

  .brand-mark {
    position: absolute; left: 50%; top: 136px; width: 82px; height: 82px;
    margin-left: -41px; background: var(--brand);
  }
  .wordmark {
    position: absolute; left: 0; right: 0; text-align: center;
    font-size: 46px; line-height: 46px; font-weight: 700; color: var(--brand); letter-spacing: 2px;
    top: 220px;
  }
</style>
</head>
<body>
<main class="stage">
  <section class="card card--front">
    <div class="holder">
      <p class="holder__name">Henrik Audun Strandvik</p>
      <address class="holder__address">Kvernbakken9,<br>6040 Fjordvik</address>
    </div>
    <ul class="contact">
      <li class="contact__item">+4791264085
        <svg viewBox="0 0 10 10"><path d="M2 0.5 L3.6 2.6 L2.6 3.6 Q3.6 5.8 6.4 7.4 L7.4 6.4 L9.5 8 L8.3 9.5 Q4 9 0.5 1.7 Z"/></svg>
      </li>
      <li class="contact__item">post@bildevold.example
        <svg viewBox="0 0 10 10"><path d="M0 2 H10 V8.5 H0 Z M0.8 2.6 L5 5.6 L9.2 2.6 Z" fill-rule="evenodd"/></svg>
      </li>
      <li class="contact__item contact__item--social">BildeVOLD <span class="contact__square"></span></li>
    </ul>
    <div class="brand-mark"></div>
    <p class="wordmark">BildeVOLD</p>
  </section>

  <section class="card card--back">
    <p class="wordmark">BildeVOLD</p>
  </section>
</main>
</body>
</html>
```